Quorva - corporate Business Card

We need a good look and innovative business card for a new start up company based in Los Angeles called "Quorva". We are in a payment business, including payment card, app, and ewallet. We are expert in online payment and Card not present (CNP) transaction.
We need an innovative, modern business card.

Our logo font is Aero Matics

Target Market(s)

Startup - Bank - Online Payment - Card Manufacturing

Industry/Entity Type

Startup

Contact Information for Business Card

phone: 555 014 7396 - Address: 4172 Marlowe blvd, Halden Park, CA 90299

Requirements
Must have
• Message: innovative, professional, expert, high tech, trust, online payment expert, security
Nice to have
• no comment
Should not have
• no Comment

```html
<!DOCTYPE html>
<html lang="en">
<head>
<meta charset="utf-8">
<title>Quorva – Business Card</title>
<link rel="stylesheet" href="https://fonts.googleapis.com/css2?family=Exo+2:wght@600&family=Lato:wght@400;700&display=swap">
<style>
  :root {
    --brand-red: #b31e2c;
    --paper: #ffffff;
    --stage: #efefef;
    --ink: #1c1c1c;
    --circle-tint: #efd3d7;
  }
  * { margin: 0; padding: 0; box-sizing: border-box; }
  html, body { width: 1200px; height: 586px; overflow: hidden; background: var(--stage); }
  .canvas { position: relative; width: 1200px; height: 586px; }

  .card {
    position: absolute; top: 129px; width: 501px; height: 300px; overflow: hidden;
  }
  .card-back { left: 61px; background: var(--brand-red); }
  .card-front { left: 619px; background: var(--paper); }

  .divider { position: absolute; left: 250px; width: 3px; background: var(--paper); }
  .divider-top { top: 0; height: 198px; }
  .divider-bottom { top: 284px; bottom: 0; }

  .wordmark {
    position: absolute; left: 0; right: 0; text-align: center;
    font-family: "Exo 2", sans-serif; font-weight: 600; font-size: 46px; line-height: 1; letter-spacing: 1.5px;
  }
  .card-back .wordmark { top: 210px; color: var(--paper); }
  .card-front .wordmark { top: 36px; color: var(--brand-red); }

  .website {
    position: absolute; top: 262px; left: 0; right: 0; text-align: center;
    font-family: "Lato", sans-serif; font-weight: 700; font-size: 11px; letter-spacing: 3.4px; color: var(--paper);
  }

  .accent-circle {
    position: absolute; left: 283px; top: 87px; width: 268px; height: 268px; border-radius: 50%;
    background: var(--circle-tint);
  }

  .holder { position: absolute; left: 27px; top: 160px; font-family: "Lato", sans-serif; }
  .holder-name { font-weight: 700; font-size: 17.5px; color: var(--brand-red); }
  .holder-role { font-size: 11.5px; color: var(--ink); margin-top: 3px; }

  .rule {
    position: absolute; left: 0; top: 205px; width: 175px; height: 3px;
    background: linear-gradient(to right, var(--brand-red), rgba(179,30,44,0));
  }

  .contact { position: absolute; left: 28px; display: flex; align-items: center; gap: 6px;
    font-family: "Lato", sans-serif; font-size: 13px; color: var(--ink); }
  .contact-phone { top: 218px; }
  .contact-email { top: 243px; }
  .contact-icon { width: 18px; height: 18px; display: block; }

  .address { position: absolute; left: 27px; top: 270px;
    font-family: "Lato", sans-serif; font-weight: 700; font-size: 12.5px; color: var(--brand-red); }
</style>
</head>
<body>
<main class="canvas">
  <section class="card card-back" aria-label="Card back">
    <span class="divider divider-top"></span>
    <span class="divider divider-bottom"></span>
    <p class="wordmark">quorva</p>
    <p class="website">www.quorvawebsite.com</p>
  </section>

  <section class="card card-front" aria-label="Card front">
    <span class="accent-circle"></span>
    <p class="wordmark">quorva</p>
    <div class="holder">
      <p class="holder-name">Marcus Henley</p>
      <p class="holder-role">Owner &amp; Founder</p>
    </div>
    <span class="rule"></span>
    <p class="contact contact-phone">
      <svg class="contact-icon" viewBox="0 0 18 18" aria-hidden="true">
        <circle cx="9" cy="9" r="9" fill="#b31e2c"/>
        <path d="M4.5 7.5c0-1.2 2-2 4.5-2s4.5.8 4.5 2v1h-2.2v-1h-4.6v1H4.5z" fill="#fff"/>
        <rect x="6" y="9" width="6" height="3.5" rx="0.6" fill="#fff"/>
      </svg>
      (555) 014-7396
    </p>
    <p class="contact contact-email">
      <svg class="contact-icon" viewBox="0 0 18 18" aria-hidden="true">
        <circle cx="9" cy="9" r="9" fill="#b31e2c"/>
        <rect x="4.5" y="6" width="9" height="6.5" fill="#fff"/>
        <path d="M4.5 6l4.5 3.6L13.5 6" fill="none" stroke="#b31e2c" stroke-width="1"/>
      </svg>
      MarcusH@quorvaweb.com
    </p>
    <p class="address">4172 Marlowe blvd, Halden Park, CA 90299</p>
  </section>
</main>
</body>
</html>
```